RW Framewell Inc Business cards

We need business cards using our existing logo but slightly modified. Right now the logo says RW Loadbearing Masonry. We want to keep the RW part of the design, but replace the Structural Concrete portion with "FRAMEWELL". Please see the attached file.
Ideally this would be a blank template so we can add Different Names, titles, and phone numbers later.
On the one side we want only the logo and on the other side the detail. I'm attaching an example for you to see.
Please reach out with any other questions. Our address and other details will be given out once we find a design we like.

Target Market(s)

Construction Industry

```html
<!DOCTYPE html>
<html lang="en">
<head>
<meta charset="utf-8">
<title>RW Framewell Inc — Business Cards</title>
<link href="https://fonts.googleapis.com/css2?family=Arimo:wght@400;700&display=swap" rel="stylesheet">
<style>
  :root {
    --backdrop: #262626;
    --card: #0b0b0c;
    --brand-blue: #1c78c8;
    --steel-grey: #8e8f92;
    --text-light: #c9cacc;
    --divider: #3a3a3c;
  }
  * { box-sizing: border-box; margin: 0; padding: 0; }
  html, body {
    width: 1200px;
    height: 900px;
    overflow: hidden;
    background: var(--backdrop);
    font-family: "Arimo", Arial, sans-serif;
  }
  .canvas {
    position: relative;
    width: 1200px;
    height: 900px;
  }
  .card {
    position: absolute;
    left: 260px;
    width: 680px;
    height: 390px;
    background: var(--card);
    box-shadow: 0 14px 30px rgba(0, 0, 0, 0.55);
  }
  .card--back { top: 40px; }
  .card--front { top: 470px; }

  /* Wordmark */
  .wordmark {
    display: flex;
    align-items: center;
    gap: 14px;
    color: var(--brand-blue);
    font-weight: 700;
    text-transform: uppercase;
    white-space: nowrap;
  }
  .wordmark__square {
    background: var(--brand-blue);
    flex: none;
  }
  .card--back .wordmark {
    position: absolute;
    left: 50%;
    top: 50%;
    transform: translate(-50%, -50%);
    font-size: 46px;
    letter-spacing: 2px;
  }
  .card--back .wordmark__square { width: 34px; height: 34px; }

  .card--front .wordmark {
    position: absolute;
    left: 40px;
    top: 50%;
    transform: translateY(-50%);
    font-size: 27px;
    letter-spacing: 1px;
    gap: 10px;
  }
  .card--front .wordmark__square { width: 20px; height: 20px; }

  .divider {
    position: absolute;
    left: 340px;
    top: 95px;
    width: 1px;
    height: 200px;
    background: var(--divider);
  }

  .details {
    position: absolute;
    left: 378px;
    top: 112px;
    color: var(--text-light);
  }
  .details__name {
    color: var(--brand-blue);
    font-size: 22px;
    font-weight: 700;
    text-transform: uppercase;
    letter-spacing: 0.3px;
  }
  .details__title {
    font-size: 17px;
    color: var(--steel-grey);
    margin-top: 2px;
  }
  .contact {
    list-style: none;
    margin-top: 30px;
  }
  .contact__item {
    display: flex;
    align-items: center;
    gap: 9px;
    font-size: 16px;
    line-height: 25px;
  }
  .contact__icon {
    width: 15px;
    height: 15px;
    flex: none;
  }
  .contact__accent { color: var(--brand-blue); }
</style>
</head>
<body>
<main class="canvas">

  <section class="card card--back" aria-label="Card back">
    <div class="wordmark">
      <span class="wordmark__square" aria-hidden="true"></span>
      <span>RW Framewell</span>
    </div>
  </section>

  <section class="card card--front" aria-label="Card front">
    <div class="wordmark">
      <span class="wordmark__square" aria-hidden="true"></span>
      <span>RW Framewell</span>
    </div>

    <div class="divider" aria-hidden="true"></div>

    <div class="details">
      <p class="details__name">Daniel Harlow</p>
      <p class="details__title">Managing Director</p>
      <ul class="contact">
        <li class="contact__item">
          <svg class="contact__icon" viewBox="0 0 16 16" aria-hidden="true">
            <path fill="var(--brand-blue)" d="M3.6 1.2l2.2 2.6-1.3 1.6c.9 2 2.3 3.4 4.2 4.3l1.6-1.3 2.6 2.2-1.4 2.3c-4.9-.6-8.6-4.3-9.2-9.2z"/>
          </svg>
          <span>044-555 010 234</span>
        </li>
        <li class="contact__item">
          <svg class="contact__icon" viewBox="0 0 16 16" aria-hidden="true">
            <rect x="1" y="3" width="14" height="10" fill="var(--brand-blue)"/>
            <path d="M1.5 3.5L8 9l6.5-5.5" fill="none" stroke="var(--card)" stroke-width="1.3"/>
          </svg>
          <span>info@framewellmail.com</span>
        </li>
        <li class="contact__item">
          <svg class="contact__icon" viewBox="0 0 16 16" aria-hidden="true">
            <g fill="none" stroke="var(--brand-blue)" stroke-width="1.3">
              <circle cx="8" cy="8" r="6.5"/>
              <ellipse cx="8" cy="8" rx="2.8" ry="6.5"/>
              <path d="M1.5 8h13M2.5 4.8h11M2.5 11.2h11"/>
            </g>
          </svg>
          <span>www.<span class="contact__accent">framewellsite</span>.com</span>
        </li>
      </ul>
    </div>
  </section>

</main>
</body>
</html>
```